Community-based social network needs a new landing page

We need a landing page for a local social network in Singapore called "LaneKindred.sg". It is a website that help neighbours to connect with each other for mutual benefits such as providing professional/non-professional services, sharing items, and neighbourly help, etc.

There is an existing website but we want to completely revamp it. It is most important that the new landing page communicates that the neighbourhood has skills and services for people to discover.

The final design of the landing page should be modern, and communicates a sense of community and vibrancy. As a matter of priority, more real estate should be accorded to the neighbours providing services elements.

We have drafted 2 reference sites that communicates the key ideas/user propositions for your easy reference:
http://tarvelquin8.example-sites.com/lanekindred
http://tarvelquin8.example-sites.com/lanekindred2

As long as the key ideas/user propositions are kept to, we are open to any design proposals. I.e. you do not have to follow the design layout of the reference sites

Target Market(s)

Our target market is primarily the Singapore community, includes all genders, education levels and occupations, aged between 17-45 years old.

In the file uploaded, you will find pictures of Singapore neighbourhoods and people of local ethnicities. Please use them, but you may arrange and add further filters to better enhance them

Industry/Entity Type

Real Estate

Requirements
Nice to have
• Landing page could be similar to that of www.gatherloft.com, not just at the top, but also the way the other categories are presented at the bottom.

```html
<!DOCTYPE html>
<html lang="en">
<head>
<meta charset="utf-8">
<title>LaneKindred.sg — Find people living near you</title>
<link rel="stylesheet" href="https://fonts.googleapis.com/css2?family=Open+Sans:wght@300;400;600;700&display=swap">
<style>
:root{
  --red:#d7262b;
  --navy:#17365d;
  --fbblue:#3c64a8;
  --coral:#f0806a;
  --lilac:#97a3dd;
  --mint:#6fcaa8;
  --teal:#2f8fa3;
  --cream:#ece8dc;
  --panel:#ececec;
  --footer:#454545;
  --ink:#2b2b2b;
  --muted:#8a8a8a;
}
*{box-sizing:border-box;margin:0;padding:0}
html,body{width:824px;height:1200px;overflow:hidden}
body{position:relative;background:var(--cream);font-family:"Open Sans",Arial,sans-serif;color:var(--ink)}
.abs{position:absolute}
.topbar{left:0;top:0;width:824px;height:5px;background:var(--red)}
.header-band{left:0;top:5px;width:824px;height:80px;background:#fff}
.header{left:69px;top:5px;width:686px;height:80px;background:#fff}
.brand{left:12px;top:30px;display:flex;align-items:center;gap:8px;font-size:22px;font-weight:700;color:var(--ink);letter-spacing:-.5px;line-height:28px}
.brand-mark{width:18px;height:18px;background:var(--red)}
.btn{top:31px;width:82px;height:22px;font-size:12px;display:flex;align-items:center;justify-content:center}
.btn-signup{left:406px;background:#e6e6e6;color:var(--ink)}
.btn-login{left:499px;background:var(--navy);color:#fff}
.btn-social{left:592px;background:var(--fbblue);color:#fff;border:1px solid #2c4f8e}
.hero{left:0;top:85px;width:824px;height:375px;
  background:
    radial-gradient(ellipse 260px 220px at 420px 190px,rgba(120,150,175,.55),rgba(120,150,175,0) 100%),
    radial-gradient(ellipse 200px 200px at 150px 230px,rgba(110,140,160,.5),rgba(110,140,160,0) 100%),
    radial-gradient(ellipse 200px 200px at 720px 220px,rgba(200,210,220,.6),rgba(200,210,220,0) 100%),
    linear-gradient(180deg,#4aa6ef 0%,#7ab9e9 14%,#a6c3d6 30%,#b3bfc8 48%,#97a6b0 64%,#c3cbd0 78%,#8f9aa0 86%,#6f8792 93%,#5e7682 100%)}
.callout{display:flex;font-size:8px;line-height:12px}
.callout .photo{flex:none;background:linear-gradient(160deg,#c9a58c,#7a5a48)}
.c1{left:69px;top:147px;width:208px;height:56px;background:#d6e9a5;color:#333}
.c1 .photo{width:56px}
.c1 p{padding:11px 6px 0 6px}
.c2{left:516px;top:234px;width:226px;height:60px;background:#a9bde8;color:#222}
.c2 .photo{width:58px}
.c2 p{padding:13px 16px 0 8px}
.c3{left:69px;top:308px;width:277px;height:72px;background:var(--teal);color:#fff}
.c3 .photo{width:73px;background:linear-gradient(160deg,#e2c196,#9b6d3e)}
.c3 p{padding:16px 22px 0 15px}
.pin{width:22px;height:22px;border-radius:50%;background:#d9d9d9;border:5px solid #9d9d9d}
.content{left:69px;top:418px;width:686px;height:549px;background:#f9f9fa}
.tagline{left:0;top:26px;width:686px;text-align:center;font-size:19.5px;font-weight:400;color:#222}
.tagline strong{color:var(--red);font-weight:600}
.divider{left:12px;top:76px;width:662px;height:4px}
.card{top:114px;width:206px;height:176px;color:#fff}
.card h3{position:absolute;left:52px;top:14px;font-size:13.5px;font-weight:400;line-height:15px}
.card .icon{position:absolute;left:14px;top:12px;width:30px;height:30px}
.card p{position:absolute;left:14px;top:64px;width:184px;font-size:10px;line-height:16.5px;font-weight:300}
.card .more{position:absolute;right:0;top:140px;width:55px;height:18px;background:rgba(255,255,255,.2);font-family:Georgia,serif;font-size:9px;display:flex;align-items:center;justify-content:center}
.card-pro{left:12px;background:var(--coral)}
.card-non{left:240px;background:var(--lilac)}
.card-help{left:469px;background:var(--mint)}
.lower{left:69px;top:752px;width:686px;height:215px;background:var(--panel)}
.lower h4{position:absolute;top:20px;font-size:11.5px;font-weight:600;color:#3a9ab8}
.member{width:46px;height:46px}
.join{left:67px;top:167px;width:98px;height:30px;background:#111;color:#fff;font-size:13.5px;display:flex;align-items:center;justify-content:center}
.posts{left:259px;top:48px;list-style:none}
.posts li{display:flex;align-items:center;gap:9px;height:21.6px;font-size:8.5px;color:var(--muted)}
.posts i{width:11px;height:9px;background:#a8a8a8;border-radius:2px}
.feature{left:491px;width:184px;height:65px}
.footer{left:0;top:967px;width:824px;height:233px;background:var(--footer);color:#fff}
.footer h5{position:absolute;font-size:11.5px;font-weight:600}
.share-box{left:81px;top:46px;width:333px;height:51px;background:#f2f2f2;border-radius:3px;font-size:7px;color:#333}
.count{position:absolute;width:36px;height:22px;background:#fff;border:1px solid #ccc;font-size:11px;display:flex;align-items:center;justify-content:center}
.mini{position:absolute;height:12px;border:1px solid #bbb;background:#fafafa;font-size:7px;display:flex;align-items:center;padding:0 4px}
.mentions{left:457px;top:40px;width:290px;font-size:8.5px;line-height:14px;color:#b5b5b5}
.mentions p+p{margin-top:7px}
.rule{left:69px;top:127px;width:686px;height:1px;background:#5a5a5a}
.about{left:81px;top:166px;width:250px;font-size:8.5px;line-height:14px;color:#b5b5b5}
.links{font-size:8.5px;line-height:12px;color:#c2c2c2;font-weight:600;list-style:none}
</style>
</head>
<body>
<div class="abs topbar"></div>
<div class="abs header-band"></div>
<header class="abs header">
  <div class="abs brand"><span class="brand-mark"></span>LaneKindred.sg</div>
  <a class="abs btn btn-signup">Sign Up</a>
  <a class="abs btn btn-login">Login</a>
  <a class="abs btn btn-social">Social Login</a>
</header>

<section class="abs hero" role="img" aria-label="Photograph of the Singapore city skyline of glass towers across the waterfront under a blue sky"></section>

<div class="abs callout c1"><div class="photo" role="img" aria-label="Photo of a neighbour holding a guitar"></div><p>Amira, a non-professional guitar enthusiast, will teach beginner guitar for only $5 per lesson</p></div>
<div class="abs pin" style="left:266px;top:190px"></div>
<div class="abs callout c2"><div class="photo" role="img" aria-label="Photo of a young architecture graduate"></div><p>Mei Lin, an architecture under graduate, will design your home from only $200</p></div>
<div class="abs pin" style="left:730px;top:283px"></div>
<div class="abs callout c3"><div class="photo" role="img" aria-label="Photo of a neighbour with her dog"></div><p>Amira, a non-professional guitar  enthusiast, will teach beginner guitar for only $5 per lesson</p></div>
<div class="abs pin" style="left:335px;top:369px"></div>

<main class="abs content">
  <h1 class="abs tagline">Find people living near you for <strong>Useful</strong> things &amp; <strong>Neighbourly</strong> help</h1>
  <svg class="abs divider" viewBox="0 0 662 4" preserveAspectRatio="none"><path d="M0 2 Q4 0 8 2 T16 2 T24 2 T32 2 T40 2 T48 2 T56 2 T64 2 T72 2 T80 2 T88 2 T96 2 T104 2 T112 2 T120 2 T128 2 T136 2 T144 2 T152 2 T160 2 T168 2 T176 2 T184 2 T192 2 T200 2 T208 2 T216 2 T224 2 T232 2 T240 2 T248 2 T256 2 T264 2 T272 2 T280 2 T288 2 T296 2 T304 2 T312 2 T320 2 T328 2 T336 2 T344 2 T352 2 T360 2 T368 2 T376 2 T384 2 T392 2 T400 2 T408 2 T416 2 T424 2 T432 2 T440 2 T448 2 T456 2 T464 2 T472 2 T480 2 T488 2 T496 2 T504 2 T512 2 T520 2 T528 2 T536 2 T544 2 T552 2 T560 2 T568 2 T576 2 T584 2 T592 2 T600 2 T608 2 T616 2 T624 2 T632 2 T640 2 T648 2 T656 2 T664 2" fill="none" stroke="#dcdcdc" stroke-width="1"/></svg>

  <article class="abs card card-pro">
    <svg class="icon" viewBox="0 0 30 30" fill="none" stroke="#fff" stroke-width="2"><path d="M8 27v-6a10 10 0 1 1 12 0v6"/><path d="M11 9l8 8M19 9l-8 8"/></svg>
    <h3>Professional<br>Services</h3>
    <p>Maecenas non nunc libero, vitae imperdiet magna roin vulputate est vitae cursus urus vel turpis gravida semper roin vulputate.</p>
    <span class="more">More</span>
  </article>
  <article class="abs card card-non">
    <svg class="icon" viewBox="0 0 30 30" fill="#fff"><circle cx="18" cy="6" r="4"/><path d="M12 12h12v10h-3v7h-6v-7h-3z"/><path d="M2 4l10 10" stroke="#fff" stroke-width="2"/></svg>
    <h3>Non Professional<br>Services</h3>
    <p>Proin elementum erat non velit hendrerit interdum pretium neque sag por interdum velit vel ultrici roin malesuada dui eget ipsum.</p>
    <span class="more">More</span>
  </article>
  <article class="abs card card-help">
    <svg class="icon" viewBox="0 0 30 30" fill="none" stroke="#fff" stroke-width="2"><path d="M4 14a10 8 0 1 1 6 7l-5 3 1-5a8 8 0 0 1-2-5z"/><path d="M14 24a9 6 0 0 0 12-6"/></svg>
    <h3>Non Professional<br>Services</h3>
    <p>Nam liber tempor cum soluta nobis eleifend option congue nihil imperdiet doming id quod mazim placerat facer possim assum.</p>
    <span class="more">More</span>
  </article>
</main>

<section class="abs lower">
  <h4 style="left:11px">Latest Members</h4>
  <div class="abs member" style="left:12px;top:50px;background:#c9b5a4" role="img" aria-label="Member photo"></div>
  <div class="abs member" style="left:64px;top:50px;background:#8a7566" role="img" aria-label="Member photo"></div>
  <div class="abs member" style="left:114px;top:50px;background:#a0504a" role="img" aria-label="Member photo"></div>
  <div class="abs member" style="left:166px;top:50px;background:#d8c2b0" role="img" aria-label="Member photo"></div>
  <div class="abs member" style="left:12px;top:103px;background:#b86a4a" role="img" aria-label="Member photo"></div>
  <div class="abs member" style="left:64px;top:103px;background:#3c2f2a" role="img" aria-label="Member photo"></div>
  <div class="abs member" style="left:114px;top:103px;background:#8b6a55" role="img" aria-label="Member photo"></div>
  <div class="abs member" style="left:166px;top:103px;background:#a8a39c" role="img" aria-label="Member photo"></div>
  <a class="abs join">Join for free</a>

  <h4 style="left:259px">Latest Posts</h4>
  <ul class="abs posts">
    <li><i></i>Jia Hui Tan has shared Measuring Tape</li>
    <li><i></i>Jia Hui Tan has shared Measuring Tape</li>
    <li><i></i>Jia Hui Tan has shared Novels</li>
    <li><i></i>Jia Hui Tan has shared Children Books</li>
    <li><i></i>Jia Hui Tan has shared Self Help Books</li>
    <li><i></i>Jia Hui Tan has shared Measuring Tape</li>
    <li><i></i>Jia Hui Tan has shared Novels</li>
  </ul>

  <h4 style="left:491px">Latest Features</h4>
  <div class="abs feature" style="top:45px;background:linear-gradient(90deg,#3a2a20,#f3efe9 40%,#e6e2da 70%,#c84a3a)" role="img" aria-label="Featured promotion banner for a coffee supplement"></div>
  <div class="abs feature" style="top:126px;background:linear-gradient(90deg,#f1c40f,#1f5fa8 35%,#0d3f80)" role="img" aria-label="Featured promotion banner for a commerce platform"></div>
</section>

<footer class="abs footer">
  <h5 style="left:79px;top:22px">If you found LaneKindred.sg useful, tell your friends about ti!</h5>
  <div class="abs share-box">
    <span class="count" style="left:5px;top:5px">21</span>
    <span class="count" style="left:49px;top:5px;color:#777">11</span>
    <span class="mini" style="left:93px;top:6px">Like</span>
    <span style="position:absolute;left:124px;top:8px">516 people like this. Be the first of your friends.</span>
    <span class="mini" style="left:5px;top:34px;font-weight:700;color:#333">Share</span>
    <span class="mini" style="left:49px;top:34px;color:var(--red)">+1</span>
  </div>
  <h5 style="left:457px;top:22px">Media Mentions</h5>
  <div class="abs mentions">
    <p>LaneKindred.sg is an initiative supported by CVSN.</p>
    <p>“LaneKindred.sg fills a critical gap, by providing a mechanism for neighbours to communicate with each  other their resources and their willingness to help.” - NMP Daniel Koh, CEO of CVSN</p>
  </div>
  <div class="abs rule"></div>
  <h5 style="left:81px;top:148px">© Hearthlane Pte Ltd 2013</h5>
  <p class="abs about">LaneKindred.sg is a website of Hearthlane Pte Ltd. We help you pool together physical items, efforts, and purchasing power with your favourite neighbours so that you can save money, free up space at home, be eco-friendly.</p>
  <h5 style="left:365px;top:148px">Want to know more?</h5>
  <ul class="abs links" style="left:365px;top:168px"><li>About us</li><li>FAQ</li></ul>
  <h5 style="left:518px;top:148px">Using Lane Kindred</h5>
  <ul class="abs links" style="left:518px;top:168px"><li>Terms of Use</li><li>Privacy Policy</li></ul>
  <h5 style="left:676px;top:148px">Get in touch</h5>
  <ul class="abs links" style="left:676px;top:168px"><li>Contact us</li><li>Friendloop</li></ul>
</footer>
</body>
</html>
```